ORLA - Óptica Médica - web design and concept

Website concept - Create and develop our website design and structure. ORLA is an optical store chain, and we are looking to establish our web and digital concept. In attachment there are several pictures about our stores and our logo.

The website structure should be user friendly. Colors should be light and the design as simple and minimalist as possible. There are different variations of the logothat can be used, check the file.

The website will include optical collections and sun collections as an online store. Also, a medical menu should be considered in order for clients to schedule optometry appointments. There should also be a menu for client assistance where the clients can read about glass maintenance in our workshop.
Updates

Low design quality

Number of Pages Required

5+ page

Font styles to use
Serif
Sans Serif

Requirements
Must have
• Must be user-friendly and minimalist.
• Please USE PICTURES FROM THE BRANDS we sell: MERUN, BOSKA, PNW, KOLE, BAMPE
Nice to have
• Nice to inspire: ZEK glasses (see website https://ch.shopzek.com/en/)
• Nice to inspire: https://merun-eyewear.com/
• Nice to ispire: https://www.pnwglobe.com/en/
Should not have
• Hysteric colors and shapes

```html
<!DOCTYPE html>
<html lang="en">
<head>
<meta charset="utf-8">
<title>ORLA Óptica Médica</title>
<link href="https://fonts.googleapis.com/css2?family=Poppins:wght@400;500;600&family=Open+Sans:wght@400;600&display=swap" rel="stylesheet">
<style>
:root{
  --black:#0b0b0b;
  --gold:#c8963e;
  --gold-light:#dcae5c;
  --ink:#2b2b2b;
  --muted:#6f6f6f;
  --line:#dddddd;
  --white:#ffffff;
  --ceiling:#3e3a37;
  --wall:#8f8a84;
  --wood:#9a6a3e;
  --floor:#e9e1d6;
}
*{margin:0;padding:0;box-sizing:border-box}
html,body{width:1200px;height:3147px;overflow:hidden}
body{position:relative;background:var(--white);font-family:"Open Sans",Arial,sans-serif;color:var(--ink)}
.abs{position:absolute}
h1,h2,h3{font-weight:500}

/* header */
.site-header{left:0;top:0;width:1200px;height:110px;background:var(--black);border-bottom:3px solid var(--gold);z-index:5}
.nav a{position:absolute;top:46px;color:var(--white);font:600 12.5px "Poppins",Arial,sans-serif;text-decoration:none;letter-spacing:.3px}
.round-btn{position:absolute;top:33px;width:46px;height:46px;border:2px solid var(--gold);border-radius:50%;display:flex;align-items:center;justify-content:center}
.logo-plate{left:505px;top:0;width:134px;height:200px;z-index:6}
.logo-name{position:absolute;left:0;top:86px;width:134px;text-align:center;font:500 36px "Poppins",Arial,sans-serif;color:var(--gold-light);letter-spacing:5px}

/* hero */
.hero{left:0;top:110px;width:1200px;height:1038px;
  background:
    radial-gradient(ellipse 360px 150px at 600px 560px,rgba(154,106,62,.85),rgba(154,106,62,0) 100%),
    linear-gradient(90deg,rgba(176,132,58,.55) 0%,rgba(176,132,58,0) 14%,rgba(176,132,58,0) 86%,rgba(176,132,58,.55) 100%),
    linear-gradient(180deg,var(--ceiling) 0%,#6a6460 18%,var(--wall) 38%,#a89c8e 56%,#d8cec2 70%,var(--floor) 84%,#f3eee8 100%)}
.hero-dots{left:573px;top:784px;display:flex;gap:6px}
.hero-dots span{width:14px;height:14px;border-radius:50%;border:2px solid var(--ink);background:var(--white)}
.hero-dots span.on{border-color:var(--gold)}
.welcome-title{left:0;top:842px;width:1200px;text-align:center;font:500 29px "Poppins",Arial,sans-serif;color:var(--ink)}
.welcome-text{left:226px;top:922px;width:748px;text-align:center;font-size:11.5px;line-height:27.5px;color:#3a3a3a}
.btn-gold{left:467px;top:1057px;width:266px;height:50px;border-radius:25px;background:linear-gradient(180deg,#d9a752,#b98230);color:var(--white);font:500 16px "Poppins",Arial,sans-serif;display:flex;align-items:center;justify-content:center}

/* section titles */
.sec-title{left:0;width:1200px;text-align:center;font:500 29px "Poppins",Arial,sans-serif}
.sec-rule{left:560px;width:80px;height:3px;background:var(--gold)}
.sec-sub{left:0;width:1200px;text-align:center;font-size:11.5px;color:var(--muted)}

/* products */
.product-card{top:1309px;width:246px;height:356px;background:var(--white);border:1px solid var(--line)}
.product-photo{width:244px;height:189px}
.product-name{margin-top:24px;text-align:center;color:var(--gold);font:500 14px "Poppins",Arial,sans-serif;letter-spacing:.5px}
.product-text{margin:16px 22px 0;height:75px;overflow:hidden;text-align:center;font-size:11px;line-height:25px;color:var(--muted)}
.cart-dot{position:absolute;left:98px;top:331px;width:48px;height:48px;border-radius:50%;background:var(--gold);display:flex;align-items:center;justify-content:center}
.slider-arrow{top:1448px}

/* guarantees */
.guarantees{left:0;top:1748px;width:1200px;height:372px;background:linear-gradient(180deg,#c2903c,#cfa453 60%,#d3ad63)}
.guarantee{top:1903px;width:170px;text-align:center}
.guarantee .ring{width:108px;height:108px;margin:0 auto;border:2px solid var(--white);border-radius:50%;display:flex;align-items:center;justify-content:center}
.guarantee p{margin-top:20px;color:var(--white);font:500 14px "Poppins",Arial,sans-serif;line-height:23px}

/* blog */
.blog-band{left:0;top:2120px;width:1200px;height:545px;background:linear-gradient(180deg,#efefef,#f7f7f7)}
.post-card{top:2243px;width:330px;height:380px;background:var(--white);box-shadow:0 1px 4px rgba(0,0,0,.18)}
.post-photo{width:330px;height:199px}
.post-title{margin:20px 20px 0;font:500 16px "Poppins",Arial,sans-serif;color:var(--ink)}
.post-date{margin:9px 20px 0;display:flex;align-items:center;gap:8px;color:var(--gold);font:500 13px "Poppins",Arial,sans-serif}
.post-text{margin:12px 20px 0;font-size:11px;line-height:25px;color:#555}

/* brands */
.brand-box{top:2782px;width:186px;height:103px;border:1px solid #cfcfcf;display:flex;align-items:center;justify-content:center;font:600 17px "Poppins",Arial,sans-serif;color:var(--black);letter-spacing:1px}

/* footer */
.site-footer{left:0;top:2941px;width:1200px;height:206px;background:var(--black)}
.footer-name{left:166px;top:3055px;width:134px;text-align:center;font:500 36px "Poppins",Arial,sans-serif;color:var(--gold-light);letter-spacing:5px}
.footer-nav a{position:absolute;top:3005px;color:var(--white);font:600 11.5px "Poppins",Arial,sans-serif;text-decoration:none}
.copyright{left:376px;top:3074px;color:var(--white);font-size:11px}
.social{top:3064px;width:36px;height:36px;border:1.5px solid var(--white);border-radius:50%}
</style>
</head>
<body>

<!-- hero -->
<div class="abs hero" role="img" aria-label="Photograph of the ORLA store interior with wooden display counter, gold-framed wall cabinets and a geometric ceiling lamp"></div>
<div class="abs hero-dots"><span></span><span class="on"></span><span></span></div>
<h1 class="abs welcome-title">Welcome to ORLA Optica</h1>
<p class="abs welcome-text">ORLA OPTICA opens its doors with a clear purpose: to take care of you. Our priority is your visual health, and for this reason we have the best professionals and the most competitive products to serve your needs.ORLA Óptica is the dream of a young entrepreneur named Marco. With a degree in optics and optometry, he has acquired knowledge and skills to provide that multi-disciplinary and demanding service that you deserve.</p>
<div class="abs btn-gold">Get to know us better!</div>

<!-- header -->
<header class="abs site-header">
  <div class="round-btn" style="left:109px">
    <svg width="16" height="14" viewBox="0 0 16 14"><path d="M1 1h3l2 8h8l1.5-6H5" fill="none" stroke="#c8963e" stroke-width="1.6"/><circle cx="7" cy="12" r="1.3" fill="#c8963e"/><circle cx="13" cy="12" r="1.3" fill="#c8963e"/></svg>
  </div>
  <nav class="nav">
    <a style="left:172px">HOME</a>
    <a style="left:275px">ABOUT US</a>
    <a style="left:403px">PRODUCTS</a>
    <a style="left:733px">CONTACT</a>
    <a style="left:857px">BLOG</a>
    <a style="left:955px">STORE</a>
  </nav>
  <div class="round-btn" style="left:1017px">
    <svg width="16" height="16" viewBox="0 0 16 16"><circle cx="6.5" cy="6.5" r="5" fill="none" stroke="#c8963e" stroke-width="1.8"/><path d="M10.3 10.3L15 15" stroke="#c8963e" stroke-width="1.8"/></svg>
  </div>
</header>
<div class="abs logo-plate">
  <svg width="134" height="200" viewBox="0 0 134 200"><path d="M0 0H134V160L67 200L0 160Z" fill="#0b0b0b"/></svg>
  <div class="logo-name">ORLA</div>
</div>

<!-- products -->
<h2 class="abs sec-title" style="top:1178px">Our Products</h2>
<div class="abs sec-rule" style="top:1230px"></div>
<p class="abs sec-sub" style="top:1252px">At ORLA Óptica we offer you personalized attention. Our professional experience, together</p>

<svg class="abs slider-arrow" style="left:40px" width="20" height="90" viewBox="0 0 20 90"><path d="M18 2L2 45L18 88" fill="none" stroke="#bdbdbd" stroke-width="1.5"/></svg>
<svg class="abs slider-arrow" style="left:1140px" width="20" height="90" viewBox="0 0 20 90"><path d="M2 2L18 45L2 88" fill="none" stroke="#bdbdbd" stroke-width="1.5"/></svg>

<div class="abs product-card" style="left:84px">
  <div class="product-photo" role="img" aria-label="Photo of a woman wearing black prescription frames" style="background:linear-gradient(135deg,#e9e4df,#8a6a58 60%,#2a201c)"></div>
  <div class="product-name">GRADUATED FRAME</div>
  <p class="product-text">For followers of the latest trends and for the most classic, in ORLA Óptica we the goggle that best suits</p>
  <div class="cart-dot"><svg width="18" height="16" viewBox="0 0 16 14"><path d="M1 1h3l2 8h8l1.5-6H5Z" fill="#fff"/><circle cx="7" cy="12" r="1.4" fill="#fff"/><circle cx="13" cy="12" r="1.4" fill="#fff"/></svg></div>
</div>
<div class="abs product-card" style="left:345px">
  <div class="product-photo" role="img" aria-label="Photo of a child trying on red glasses" style="background:linear-gradient(135deg,#dfe6e6,#e9c9b5 55%,#d9b59a)"></div>
  <div class="product-name">SPECIAL CHILDREN</div>
  <p class="product-text">Did you know that a high percentage of children suffer from some type of Detecting visual deficit</p>
  <div class="cart-dot"><svg width="18" height="16" viewBox="0 0 16 14"><path d="M1 1h3l2 8h8l1.5-6H5Z" fill="#fff"/><circle cx="7" cy="12" r="1.4" fill="#fff"/><circle cx="13" cy="12" r="1.4" fill="#fff"/></svg></div>
</div>
<div class="abs product-card" style="left:605px">
  <div class="product-photo" role="img" aria-label="Photo of two clear ophthalmic lenses" style="background:radial-gradient(circle at 50% 50%,#ffffff,#e8e8e8 60%,#cfcfcf)"></div>
  <div class="product-name">OPHTHALMIC LENSES</div>
  <p class="product-text">We guarantee our clients a personalized attention, advising them the most suitable type of lens for their</p>
  <div class="cart-dot"><svg width="18" height="16" viewBox="0 0 16 14"><path d="M1 1h3l2 8h8l1.5-6H5Z" fill="#fff"/><circle cx="7" cy="12" r="1.4" fill="#fff"/><circle cx="13" cy="12" r="1.4" fill="#fff"/></svg></div>
</div>
<div class="abs product-card" style="left:866px">
  <div class="product-photo" role="img" aria-label="Photo of a smiling couple wearing sunglasses" style="background:linear-gradient(135deg,#f2a23a,#e07a2a 50%,#b95a2a)"></div>
  <div class="product-name">SUN GLASSES</div>
  <p class="product-text">Protect yourself adequately from ultraviolet (UV) rays thanks to our wide ran glasses, photochromic lenses</p>
  <div class="cart-dot"><svg width="18" height="16" viewBox="0 0 16 14"><path d="M1 1h3l2 8h8l1.5-6H5Z" fill="#fff"/><circle cx="7" cy="12" r="1.4" fill="#fff"/><circle cx="13" cy="12" r="1.4" fill="#fff"/></svg></div>
</div>

<!-- guarantees -->
<section class="abs guarantees" role="img" aria-label="Faint photograph of the store interior under a gold tint"></section>
<h2 class="abs sec-title" style="top:1768px;color:var(--white)">Our Guarantees</h2>
<div class="abs sec-rule" style="top:1820px;background:var(--white)"></div>
<p class="abs sec-sub" style="top:1842px;color:var(--white)">At ORLA Óptica we offer you personalized attention. Our professional experience, together</p>

<div class="abs guarantee" style="left:105px">
  <div class="ring"><svg width="48" height="48" viewBox="0 0 48 48"><circle cx="24" cy="12" r="7" fill="#fff"/><path d="M12 42V28a12 10 0 0 1 24 0v14Z" fill="#fff"/></svg></div>
  <p>ORLA Childhood<br>Guarantee</p>
</div>
<div class="abs guarantee" style="left:311px">
  <div class="ring"><svg width="50" height="44" viewBox="0 0 50 44"><path d="M25 4L47 40H3Z" fill="none" stroke="#fff" stroke-width="3.5" stroke-linejoin="round"/><path d="M25 16v12" stroke="#fff" stroke-width="3.5"/><circle cx="25" cy="34" r="2.2" fill="#fff"/></svg></div>
  <p>ORLA Accident<br>Warranty</p>
</div>
<div class="abs guarantee" style="left:516px">
  <div class="ring"><svg width="44" height="50" viewBox="0 0 44 50"><path d="M22 3L40 10V24C40 36 32 44 22 47C12 44 4 36 4 24V10Z" fill="none" stroke="#fff" stroke-width="3.5"/><path d="M14 25l6 6 11-12" fill="none" stroke="#fff" stroke-width="3.5"/></svg></div>
  <p>ORLA Security</p>
</div>
<div class="abs guarantee" style="left:722px">
  <div class="ring"><svg width="56" height="34" viewBox="0 0 56 34"><path d="M3 17C12 5 44 5 53 17C44 29 12 29 3 17Z" fill="none" stroke="#fff" stroke-width="3.5"/><circle cx="28" cy="17" r="7" fill="#fff"/></svg></div>
  <p>ORLA Vision</p>
</div>
<div class="abs guarantee" style="left:928px">
  <div class="ring"><svg width="40" height="48" viewBox="0 0 40 48"><rect x="4" y="3" width="32" height="42" rx="3" fill="none" stroke="#fff" stroke-width="3.5"/><path d="M11 15h18M11 23h18M11 31h12" stroke="#fff" stroke-width="3"/></svg></div>
  <p>Manufacturer's<br>Warranty</p>
</div>

<!-- blog -->
<section class="abs blog-band"></section>
<h2 class="abs sec-title" style="top:2164px;font-size:25px">Are you going to miss the last posts of the blog?</h2>
<div class="abs sec-rule" style="top:2212px"></div>

<article class="abs post-card" style="left:84px">
  <div class="post-photo" role="img" aria-label="Video thumbnail of the optician presenting a post about how we see colour" style="background:linear-gradient(120deg,#3a3330,#6b4a8c 45%,#e0b23a 75%,#3aa0d8)"></div>
  <h3 class="post-title">What color are the Bananas?</h3>
  <div class="post-date"><svg width="13" height="13" viewBox="0 0 13 13"><rect x="1" y="2" width="11" height="10" rx="1" fill="none" stroke="#c8963e" stroke-width="1.4"/><path d="M1 5h11M4 0v3M9 0v3" stroke="#c8963e" stroke-width="1.4"/></svg>JUNE 12, 2018</div>
  <p class="post-text">Si normalmente sigues el canal del Óptico de Vidora es probable que ya hayas visto el video sobre el daltonismo. En él nuestro óptico hablaba</p>
</article>
<article class="abs post-card" style="left:434px">
  <div class="post-photo" role="img" aria-label="Photo of the store interior with display counter" style="background:linear-gradient(180deg,#1e2a33,#4a5560 45%,#9a7a4a 75%,#5a4330)"></div>
  <h3 class="post-title">What color are the Bananas?</h3>
  <div class="post-date"><svg width="13" height="13" viewBox="0 0 13 13"><rect x="1" y="2" width="11" height="10" rx="1" fill="none" stroke="#c8963e" stroke-width="1.4"/><path d="M1 5h11M4 0v3M9 0v3" stroke="#c8963e" stroke-width="1.4"/></svg>JUNE 12, 2018</div>
  <p class="post-text">Si normalmente sigues el canal del Óptico de Vidora es probable que ya hayas visto el video sobre el daltonismo. En él nuestro óptico hablaba</p>
</article>
<article class="abs post-card" style="left:785px">
  <div class="post-photo" role="img" aria-label="Video thumbnail of the optician presenting a post about sun protection" style="background:linear-gradient(120deg,#e8e4d8,#c7a07a 40%,#e8d83a 70%,#b02a8a)"></div>
  <h3 class="post-title">What color are the Bananas?</h3>
  <div class="post-date"><svg width="13" height="13" viewBox="0 0 13 13"><rect x="1" y="2" width="11" height="10" rx="1" fill="none" stroke="#c8963e" stroke-width="1.4"/><path d="M1 5h11M4 0v3M9 0v3" stroke="#c8963e" stroke-width="1.4"/></svg>JUNE 12, 2018</div>
  <p class="post-text">Si normalmente sigues el canal del Óptico de Vidora es probable que ya hayas visto el video sobre el daltonismo. En él nuestro óptico hablaba</p>
</article>

<!-- brands -->
<h2 class="abs sec-title" style="top:2696px;font-size:25px">Our Brands</h2>
<div class="abs sec-rule" style="top:2740px"></div>
<div class="abs brand-box" style="left:84px">WARDEN</div>
<div class="abs brand-box" style="left:295px">LINO VESK</div>
<div class="abs brand-box" style="left:506px">CALDERA</div>
<div class="abs brand-box" style="left:717px">MIRA TORRES</div>
<div class="abs brand-box" style="left:928px">VELOCE</div>

<!-- footer -->
<footer class="abs site-footer"></footer>
<div class="abs footer-name">ORLA</div>
<nav class="footer-nav">
  <a style="left:376px">HOME</a>
  <a style="left:485px">ABOUT US</a>
  <a style="left:620px">PRODUCTS</a>
  <a style="left:758px">CONTACT</a>
  <a style="left:888px">BLOG</a>
  <a style="left:992px">STORE</a>
</nav>
<p class="abs copyright">© Copyright-2018 ORLA Optica. All rights reserved</p>
<div class="abs social" style="left:834px" aria-label="Social link"></div>
<div class="abs social" style="left:877px" aria-label="Social link"></div>
<div class="abs social" style="left:920px" aria-label="Social link"></div>
<div class="abs social" style="left:963px" aria-label="Social link"></div>
<div class="abs social" style="left:1006px" aria-label="Social link"></div>

</body>
</html>
```